Computer consultant business card

Bexil Software is a newly started computer consulting company. It's a small one-man company that provides mostly Vornix applications but also websites in collaboration with designers. I'm running this company on the side of full time university studies.

I want the final design to be clean and memorable. Be creative! :)

Some inspiration:
http://www.pixelmarta.com/design/48317
http://www.pixelmarta.com/design/2739164/business-card-design-by-frostlynk
http://www.pixelmarta.com/design/604281/business-card-design-by-koralind-vestrabanu

See attachment for my company logo.
Updates

I would like to thank everyone for submitting! I'll need a couple of days to review and ultimately select a design.

Target Market(s)

Non-technical entrepreneurs and small companies.

Industry/Entity Type

University

Requirements
Must have
• My company logo.
In any way, both colors from my logo.
First- and last name, e-mail and phone number.
Double-sided design.
Nice to have
• Something creative with the symbol in my logo

```html
<!DOCTYPE html>
<html lang="en">
<head>
<meta charset="utf-8">
<title>Zuvrel – Business Card</title>
<link rel="stylesheet" href="https://fonts.googleapis.com/css2?family=Exo+2:wght@400;600&display=swap">
<style>
  :root {
    --stage: #2a2a2b;
    --card-light: #f1f1f2;
    --card-light-shade: #dcdcde;
    --card-dark: #0d0d0e;
    --card-dark-lift: #262628;
    --ink: #3a3a3c;
    --bar: #353537;
    --bar-text: #e8e8ea;
    --blue: #4b80d4;
    --logo-grey: #4d4d50;
  }
  * { box-sizing: border-box; margin: 0; padding: 0; }
  html, body { width: 1200px; height: 900px; overflow: hidden; }
  body {
    background: var(--stage);
    font-family: "Exo 2", sans-serif;
    position: relative;
  }
  .card {
    position: absolute;
    left: 290px;
    width: 620px;
    height: 354px;
    border-radius: 4px;
    overflow: hidden;
    box-shadow: 0 18px 40px rgba(0,0,0,.45);
  }
  .card--front { top: 66px; background: linear-gradient(135deg, var(--card-light) 0%, #fafafa 45%, var(--card-light-shade) 100%); }
  .card--back  { top: 480px; background: var(--card-dark); }

  .texture-light {
    position: absolute; inset: 0;
    background: linear-gradient(160deg, rgba(255,255,255,0) 30%, rgba(200,200,205,.35) 100%);
  }

  .brand {
    position: absolute;
    display: flex; align-items: center; gap: 14px;
    font-weight: 600;
    color: var(--logo-grey);
    white-space: nowrap;
  }
  .brand__dot { width: 52px; height: 52px; border-radius: 50%; background: var(--blue); flex: none; }
  .card--front .brand { left: 300px; top: 48px; font-size: 70px; line-height: 1; }

  .name-bar {
    position: absolute; left: 0; top: 150px;
    width: 440px; height: 46px;
    background: var(--bar);
    border-radius: 0 23px 23px 0;
    display: flex; align-items: center; justify-content: flex-end;
    padding-right: 28px;
    color: var(--bar-text);
    font-size: 28px; letter-spacing: 3px; font-weight: 400;
  }
  .accent-band {
    position: absolute; left: 0; right: 0; top: 196px; height: 12px;
    background: var(--blue);
  }
  .contacts {
    position: absolute; left: 0; top: 216px;
    list-style: none;
  }
  .contacts li {
    display: flex; align-items: center; gap: 14px;
    height: 34px;
    font-size: 19px; color: var(--ink);
    white-space: nowrap;
  }
  .contacts li:nth-child(1) { padding-left: 56px; }
  .contacts li:nth-child(2) { padding-left: 28px; }
  .contacts li:nth-child(3) { padding-left: 0; }
  .contacts .web { color: var(--blue); }
  .icon-box {
    width: 28px; height: 28px; flex: none;
    background: var(--bar);
    display: flex; align-items: center; justify-content: center;
  }
  .contacts li:nth-child(3) .icon-box { background: var(--blue); }
  .icon-box svg { width: 18px; height: 18px; }

  .pattern-dark {
    position: absolute; inset: 0;
    background:
      radial-gradient(ellipse at 70% 30%, rgba(70,70,74,.55) 0%, rgba(20,20,22,0) 60%),
      linear-gradient(200deg, var(--card-dark-lift) 0%, var(--card-dark) 70%);
  }
  .card--back .brand { left: 40px; top: 214px; font-size: 62px; line-height: 1; }
  .card--back .brand__dot { width: 46px; height: 46px; }
  .back-url {
    position: absolute; left: 100px; top: 290px;
    font-size: 16px; letter-spacing: 4px; color: var(--blue);
    white-space: nowrap;
  }
</style>
</head>
<body>
  <section class="card card--front" aria-label="Card front">
    <div class="texture-light" role="img" aria-label="Faint repeating brand-symbol pattern"></div>
    <div class="brand"><span class="brand__dot"></span><span>zuvrel</span></div>
    <div class="name-bar">JOHNNY DOE</div>
    <div class="accent-band"></div>
    <ul class="contacts">
      <li>
        <span class="icon-box">
          <svg viewBox="0 0 24 24" fill="#fff"><path d="M6.6 10.8a15.1 15.1 0 0 0 6.6 6.6l2.2-2.2a1 1 0 0 1 1-.25 11.4 11.4 0 0 0 3.6.57 1 1 0 0 1 1 1V20a1 1 0 0 1-1 1A17 17 0 0 1 3 4a1 1 0 0 1 1-1h3.5a1 1 0 0 1 1 1c0 1.25.2 2.45.57 3.57a1 1 0 0 1-.25 1z"/></svg>
        </span>
        <span>+ (00) 481 739 2065</span>
      </li>
      <li>
        <span class="icon-box">
          <svg viewBox="0 0 24 24" fill="none" stroke="#fff" stroke-width="2"><rect x="3" y="5" width="18" height="14" rx="1"/><path d="M3 6l9 7 9-7"/></svg>
        </span>
        <span>johnny@zuvrel.com.au</span>
      </li>
      <li>
        <span class="icon-box">
          <svg viewBox="0 0 24 24" fill="none" stroke="#fff" stroke-width="2"><circle cx="12" cy="12" r="9"/><path d="M3 12h18M12 3c3 3 3 15 0 18M12 3c-3 3-3 15 0 18"/></svg>
        </span>
        <span class="web">www.zuvrel.com.au</span>
      </li>
    </ul>
  </section>

  <section class="card card--back" aria-label="Card back">
    <div class="pattern-dark" role="img" aria-label="Dark repeating brand-symbol pattern with glossy highlight"></div>
    <div class="brand"><span class="brand__dot"></span><span>zuvrel</span></div>
    <div class="back-url">www.zuvrel.com.au</div>
  </section>
</body>
</html>
```